Business Card Design for a Personal Trainer

I need a business card design for my job as a personal trainer. It should have a unique, modern and exclusive design. On the front there should be only my logo with my name and my job. 0162/3819204 Tobias Lendhart Wiesengrundweg 14 80417 Munich Germany The most important contact information is the web adress. it can be bigger than the rest, but its not necessary. The card should be 8,5cmx5,5cm big. Font: Roboto. Colors: black, white, gray, 56c1ff.

```html
<!DOCTYPE html>
<html lang="de">
<head>
<meta charset="utf-8">
<title>Tobias Lendhart – Personal Trainer Visitenkarte</title>
<link rel="stylesheet" href="https://fonts.googleapis.com/css2?family=Roboto:wght@300;400;500;700&display=swap">
<style>
  :root {
    --stage: #2b2b2d;
    --card: #0d0d0e;
    --card-edge: #1a1a1b;
    --white: #ffffff;
    --gray: #8a8a8c;
    --rule: #4a4a4c;
    --accent: #56c1ff;
  }
  * { margin: 0; padding: 0; box-sizing: border-box; }
  html, body {
    width: 1200px; height: 900px; overflow: hidden;
    background: var(--stage);
    font-family: "Roboto", Arial, sans-serif;
    color: var(--white);
  }
  .stage {
    width: 1200px; height: 900px;
    display: flex; flex-direction: column;
    align-items: center; justify-content: center; gap: 40px;
  }
  .card {
    position: relative;
    width: 560px; height: 362px;
    background: linear-gradient(160deg, var(--card-edge), var(--card) 60%);
    overflow: hidden;
    box-shadow: 0 14px 30px rgba(0,0,0,.45);
  }
  .card__stripe {
    position: absolute; left: 0; right: 0; bottom: 0;
    height: 12px; background: var(--accent);
  }

  /* Front */
  .front {
    display: flex; flex-direction: column;
    align-items: center; justify-content: center;
  }
  .brand { display: flex; align-items: center; gap: 16px; margin-bottom: 10px; }
  .brand__square { width: 22px; height: 22px; background: var(--white); }
  .brand__name {
    font-size: 40px; font-weight: 400; letter-spacing: 1px;
    text-transform: uppercase;
  }
  .role {
    display: flex; align-items: center; gap: 10px;
    font-size: 15px; font-weight: 400; letter-spacing: 7px;
    text-transform: uppercase;
  }
  .role::before, .role::after {
    content: ""; width: 48px; height: 1px; background: var(--white);
  }

  /* Back */
  .portrait {
    position: absolute; left: 0; top: 70px; bottom: 12px; width: 270px;
    background: radial-gradient(ellipse at 50% 40%, #8c8c8c 0%, #4d4d4d 45%, #1a1a1a 80%, transparent 100%);
  }
  .contact {
    position: absolute; left: 290px; top: 150px;
    font-size: 17px; font-weight: 400; line-height: 1.3;
  }
  .contact__row { display: flex; align-items: center; gap: 6px; }
  .contact__row svg { width: 14px; height: 14px; fill: var(--white); flex: none; }
  .contact__address { margin-top: 4px; }
  .web {
    position: absolute; left: 290px; top: 270px; width: 240px;
    padding-top: 10px; border-top: 1px solid var(--rule);
    font-size: 19px; font-weight: 700;
  }
</style>
</head>
<body>
<main class="stage">
  <section class="card front" aria-label="Vorderseite">
    <div class="brand">
      <span class="brand__square"></span>
      <span class="brand__name">Tobias Lendhart</span>
    </div>
    <p class="role">Personal Trainer</p>
    <span class="card__stripe"></span>
  </section>

  <section class="card back" aria-label="Rückseite">
    <div class="portrait" role="img" aria-label="Schwarz-weißes Porträtfoto des Trainers im Sportshirt"></div>
    <div class="contact">
      <p class="contact__row">
        <svg viewBox="0 0 24 24" aria-hidden="true"><path d="M6.6 10.8a15 15 0 0 0 6.6 6.6l2.2-2.2a1 1 0 0 1 1-.25 11.4 11.4 0 0 0 3.6.57 1 1 0 0 1 1 1V20a1 1 0 0 1-1 1A17 17 0 0 1 3 4a1 1 0 0 1 1-1h3.5a1 1 0 0 1 1 1c0 1.25.2 2.45.57 3.57a1 1 0 0 1-.25 1z"/></svg>
        0162/3819204
      </p>
      <p class="contact__row">
        <svg viewBox="0 0 24 24" aria-hidden="true"><path d="M2 5h20v14H2zm2 2v.4l8 5 8-5V7zm0 2.8V17h16V9.8l-8 5z"/></svg>
        t.lendhart@mailbox.de
      </p>
      <p class="contact__address">Wiesengrundweg 14<br>80417 München</p>
    </div>
    <p class="web">www.tobiaslendhart.de</p>
    <span class="card__stripe"></span>
  </section>
</main>
</body>
</html>
```